Ten-Harvest Brochure

We would like a 3 panel layout format with copy on both sides and on each panel, (we will provide content).

We are Ten-Harvest and we work with business owners to achieve measurable growth and success based on 5 Core Pillars Of Momentum and (S.L.K) 60 Week Progress Roadmap Scheme. We also work with the business leader and individuals within the organization with personal development.

We would like the brochure to have a corporate feel, but warm and inviting. We don't want a hard or aggressive feel.

We would like it to be available for pdf upload and physical print formats.

The winning design will also be invited to design a header for our website as well. The header will be consistent with the brochure, so please keep that in mind during your creative process.

I am enclosing a transparent copy of our company logo along with content for the brochure.

Thank you in advance for your consideration!

Gareth and Moira
Updates

Sorry, but we forgot to include the front cover text.

It will read as follows,

Do you know The 5 Core Pillars of Momentum  that are crucial to the success of any business today?

Also, please add the following to the back page

Website: www.ten-harvest.example
Resource Centre: www.thresourcehub.example 
Phone: +44 (0) 7612583047
Email: info@ten-harvest.example

Follow us on (please insert Facebook, Linkedin and YouTube logo)

I have uploaded a pdf format of brochure text.

Hello designers. I wanted to give some further input to help the process. Although the brochure is to target business, we don't want to over do it with corporate professioanls in all the photos. If there is an opportunity to incorporate photos of small business owners like, a butcher, baker, chef, flower shop etc. This would hopefully help us make an immpression to all small business owners.

Thank you, and good luck!

Gareth and Moira  

Reason: A few designers have come come on board last minute. So I'd like to give everyone the same opportunity to respond. Sincerely, Gareth

Target Market(s)

Small Business Owners searching for new ways to grow their business in the UK and Republic Of Ireland.

Industry/Entity Type

Business

```html
<!DOCTYPE html>
<html lang="en">
<head>
<meta charset="utf-8">
<title>Ten-Harvest Brochure – Inside Spread</title>
<link rel="stylesheet" href="https://fonts.googleapis.com/css2?family=PT+Sans:wght@400;700&display=swap">
<style>
  :root {
    --backdrop: #e4e2e0;
    --panel-top: #f2f1f3;
    --panel-bottom: #dddce0;
    --band-light: #8a898d;
    --band-dark: #6e6d72;
    --footer-grey: #6f6e73;
    --purple: #6a1f72;
    --link-blue: #4a4fae;
    --ink: #3d3c40;
    --ink-soft: #4a494d;
    --brand-pink: #e9c6de;
    --white: #ffffff;
  }
  * { box-sizing: border-box; margin: 0; padding: 0; }
  html, body {
    width: 1200px; height: 960px; overflow: hidden;
    background: var(--backdrop);
    font-family: "PT Sans", "Trebuchet MS", sans-serif;
    color: var(--ink);
  }
  .spread {
    position: absolute; left: 30px; top: 40px;
    width: 1140px; height: 880px;
    display: flex;
    box-shadow: 0 10px 30px rgba(0,0,0,.25);
  }
  .panel {
    position: relative; width: 380px; height: 100%; overflow: hidden;
    background: linear-gradient(180deg, var(--panel-top) 0%, var(--panel-bottom) 100%);
  }
  .panel + .panel { border-left: 1px solid rgba(0,0,0,.06); }
  .panel__photo { height: 220px; width: 100%; }
  .photo--meeting { background: linear-gradient(135deg, #efeae4 0%, #c9c4c0 45%, #3d4048 80%, #6b6f78 100%); }
  .photo--handshake { background: linear-gradient(160deg, #1f1f22 0%, #e9e4df 40%, #d3a890 60%, #f3f3f4 100%); }
  .photo--puzzle { background: linear-gradient(135deg, #3f6a2e 0%, #e7c53b 35%, #d63a4a 55%, #3a74c4 75%, #2a3342 100%); }

  .panel__band {
    position: relative; height: 55px;
    background: linear-gradient(180deg, var(--band-light), var(--band-dark));
    display: flex; align-items: center; justify-content: center;
  }
  .panel__band::after {
    content: ""; position: absolute; left: 50%; bottom: -10px;
    margin-left: -10px;
    border-left: 10px solid transparent; border-right: 10px solid transparent;
    border-top: 10px solid var(--band-dark);
  }
  .panel__title { color: var(--white); font-size: 21px; font-weight: 700; letter-spacing: .2px; }

  .panel__body { padding: 44px 30px 0 32px; font-size: 14px; line-height: 1.4; color: var(--ink-soft); }
  .panel--about .panel__body { padding-top: 56px; }
  .panel__body p + p { margin-top: 16px; }
  .link { color: var(--link-blue); font-style: italic; }
  .strong { font-weight: 700; color: var(--ink); }
  .accent { font-weight: 700; color: var(--purple); }
  .subhead { font-size: 16px; font-weight: 700; color: var(--ink); margin: 16px 0 12px; }
  .pillars { list-style: none; margin: 16px 0 18px 110px; }
  .pillars li::before { content: "-  "; white-space: pre; }
  .services { list-style: none; margin-top: 14px; }

  .resource {
    position: absolute; left: 24px; right: 24px; top: 610px;
    padding: 12px 16px 16px;
    background: rgba(255,255,255,.45);
    text-align: center; font-size: 13.5px; line-height: 1.45;
  }
  .resource__title { font-size: 15px; font-weight: 700; color: var(--ink); margin-bottom: 10px; }

  .brand {
    position: absolute; left: 34px; bottom: 56px;
    display: flex; align-items: center; gap: 10px;
  }
  .brand__mark { width: 18px; height: 18px; background: var(--brand-pink); }
  .brand__name { font-size: 26px; font-weight: 700; color: var(--brand-pink); }

  .panel__footer { position: absolute; left: 0; right: 0; bottom: 0; height: 30px; background: var(--footer-grey); }
  .panel--solutions .panel__footer { background: var(--purple); }
</style>
</head>
<body>
  <main class="spread">
    <section class="panel panel--about">
      <div class="panel__photo photo--meeting" role="img" aria-label="Photo of a businesswoman presenting a bar chart to seated colleagues"></div>
      <div class="panel__band"><h2 class="panel__title">Helping Your Business</h2></div>
      <div class="panel__body">
        <p>Recently there has been a growing trend in small business owners enlisting outside sources to help them find ways to grow and promote their businesses. At Ten-Harvest we have over 30 years combined experience in management, ownership and consulting in a wide array of businesses. We know what works and what doesn’t, and being entrepreneurs ourselves, we know first hand the struggles that can come with owning a business. Our latest venture saw us grow a new construction company from zero to over 6 MILLION in revenues in just under 2 years. This was achieved through the implementation of our unique sales, marketing and customer service strategies. Our genuine desire to help businesses and individuals succeed is what Ten-Harvest is all about.</p>
      </div>
      <div class="brand">
        <span class="brand__mark"></span>
        <span class="brand__name">Ten-Harvest</span>
      </div>
      <div class="panel__footer"></div>
    </section>

    <section class="panel panel--start">
      <div class="panel__photo photo--handshake" role="img" aria-label="Photo of two business people shaking hands over a desk"></div>
      <div class="panel__band"><h2 class="panel__title">Getting Started</h2></div>
      <div class="panel__body">
        <p>The first step is to visit <span class="link">www.ten-harvest.example</span> or call <span class="strong">07612583047</span> to book your <span class="strong">FREE CONSULTATION</span>. This will be an opportunity for you to think about where you want your business to go and for us to establish how we can help you get there.</p>
        <h3 class="subhead">After That?</h3>
        <p>We will carry out a business analysis based on <span class="accent">The 5 Core Pillars</span> of Momentum:</p>
        <ul class="pillars">
          <li>Your Brand</li>
          <li>Sales</li>
          <li>Your People</li>
          <li>Product and Service</li>
          <li>Psychology and Skills</li>
          <li>Finance</li>
        </ul>
        <p>We then provide you with a detailed report and work with you to create and implement your Progress Roadmap Scheme (S.L.K). This is a 60 week plan, customized for your business and designed so you can start seeing positive and measurable results immediately.</p>
      </div>
      <div class="panel__footer"></div>
    </section>

    <section class="panel panel--solutions">
      <div class="panel__photo photo--puzzle" role="img" aria-label="Photo of hands joining four coloured puzzle pieces"></div>
      <div class="panel__band"><h2 class="panel__title">Business Solutions</h2></div>
      <div class="panel__body">
        <p>In addition to the Total Business Analysis / S.L.K package, we also offer other business solutions which can be used individually or bundled together to create a package suitable for your needs.</p>
        <ul class="services">
          <li>One on one business mentoring</li>
          <li>Marketing strategies</li>
          <li>Sales training (individual or group)</li>
          <li>Management training (individual or group)</li>
          <li>Customer service training (individual or group)</li>
        </ul>
      </div>
      <aside class="resource">
        <h3 class="resource__title">Resource Centre</h3>
        <p>At Ten-Harvest, we are dedicated to providing current and relevant information through our resource centre www.thresourcehub.example where you will find access to videos, reports, statistics and newsletters. You will also find details on upcoming events, such as webinars, workshops and online training.</p>
      </aside>
      <div class="panel__footer"></div>
    </section>
  </main>
</body>
</html>
```